Dietary supplement, Clean and simple.

Hi,
I’d like to talk about the project,

About us:
We are a dietary supplement (Vitamins, Minerals, amino acids etc.) company.
The goal is to have about 25 products at the end of this year. However, for this goal to be achieved we need a good label design to make our products represent our company values.
I’ll be here every day supporting your questions, we are fully committed to making the highest/best quality/customer experience possible.

About the design and our values:
- Professional (We are in the industry of professionalism and expertise. I would love to show we are competent at this, Id. Like to have the labels looks like we have done our research.)
- Efficient (White spacing, good use of the space available.)
- Simple (Straight forward, in 5 seconds they have to know what the product they have is/how functions. We’re trying to simplify it for the consumer.
- No distractions (the only visually “distracting” factor can be the vector art.)

The guidelines:
The goal is to have a universal design, with one element that changes (Vector art). I’ll attach a file/multiple files I think can show some visuals on what I’m looking for, and what parts of the design I think are good/bad.

Label size: 69x155mm (Front is 77.5mm)

Design whatever you think fits our image. You’re the design expert, all I care about is that it fits our company standards/image.

Use this color/font.
Font: Sans Serif
Main company color is Mind green #237D62 (Use this color for something in the design.)

What I thought would be cool/might looks ugly, who knows:
1. The front of the label: Should have 1 vector art, preferably in the top right corner. (That looks good in multiple colors. The vector can have multiple areas to color, I would prefer 2 main colors in the vector art. The interchangeable colors are used for multiple kinds of products.)
2. Text/product information on the left. The text that will have to be displayed:
- Product name for instance “Magnesium + B6”
- Description for the product for instance “Magnesium with ginger taste”
- Company name or logo. (Add ® behind it. We are soon to be trademark registered.)
3. We need to show the "daily intake" amount on the front and also the amount in the complete bottle. For instance, “Daily intake 1 capsule, 60 capsules”.
• You don’t have to design the backside of the label. After I chose a design, I’d like to chat and give specific information on what areas need to be assigned where. (Too complex because of the law.)
Updates

Hi, Please make the deadline 31 days total. I want designers to have the time to design. And not be rushed to finish it.

I want to extend the deadline because i feel like a slightly more medical look would be interesting. Hope you can come up with something!!

Target Market(s)

Dietary supplement consumers

Industry/Entity Type

Dietary supplements

Font styles to use
Sans Serif

Colors

Designer to choose colors to be used in the design.

Requirements
Must have
• Trademark icon "®" has to be at the top right after the company logo(text of logo)/name.

```html
<!DOCTYPE html>
<html lang="en">
<head>
<meta charset="utf-8">
<title>Noble Calm – Magnesium + B6 Label</title>
<link href="https://fonts.googleapis.com/css2?family=Barlow+Semi+Condensed:wght@400;500;600&family=Barlow:wght@400;500&display=swap" rel="stylesheet">
<style>
  :root {
    --backdrop: #e8e8e6;
    --label: #f7f8f8;
    --ink: #2b2b2b;
    --ink-soft: #5e5e5e;
    --brand-grey: #626262;
    --brand-green: #237d62;
    --accent: #e6ba45;
    --accent-light: #f4d98a;
    --accent-deep: #d9913f;
    --band-text: #fdf3cf;
  }
  * { margin: 0; padding: 0; box-sizing: border-box; }
  html, body {
    width: 1200px; height: 1200px; overflow: hidden;
    background: var(--backdrop);
  }
  .label {
    position: absolute; left: 250px; top: 165px;
    width: 700px; height: 870px;
    background: linear-gradient(100deg, #fbfbfb 0%, var(--label) 40%, #ececec 100%);
    border-radius: 6px;
  }
  .brand {
    position: absolute; left: 118px; top: 158px;
    display: flex; align-items: center; gap: 12px;
    font-family: "Barlow Semi Condensed", sans-serif;
    font-weight: 600; color: var(--brand-grey);
  }
  .brand-dot {
    width: 18px; height: 18px; border-radius: 50%;
    background: var(--brand-green);
  }
  .brand-name { font-size: 40px; letter-spacing: 1px; line-height: 1; white-space: nowrap; }
  .brand-name sup { font-size: 20px; vertical-align: 20px; margin-left: 2px; }
  .product-art {
    position: absolute; left: 408px; top: 38px;
    width: 262px; height: 338px;
  }
  .product-name {
    position: absolute; left: 113px; top: 488px;
    font-family: "Barlow Semi Condensed", sans-serif;
    font-weight: 600; font-size: 76px; color: var(--ink);
    letter-spacing: 0.5px; line-height: 1;
  }
  .product-desc {
    position: absolute; left: 114px; top: 600px;
    width: 474px; height: 46px;
    background: var(--accent);
    color: var(--band-text);
    font-family: "Barlow", sans-serif; font-weight: 500;
    font-size: 25px; letter-spacing: 3.2px;
    display: flex; align-items: center; justify-content: center;
    white-space: nowrap;
  }
  .dosage {
    position: absolute; left: 114px; top: 735px;
    display: flex; align-items: baseline; gap: 10px;
    font-family: "Barlow Semi Condensed", sans-serif;
    color: var(--ink-soft); white-space: nowrap;
  }
  .dosage .count { font-size: 54px; font-weight: 600; color: var(--ink-soft); line-height: 1; }
  .dosage .unit { font-size: 26px; font-weight: 400; }
  .dosage .divider {
    width: 13px; height: 13px; background: var(--ink);
    display: inline-block; margin: 0 8px; align-self: center;
  }
  .dosage .intake { font-size: 27px; font-weight: 400; color: var(--ink); }
  .category {
    position: absolute; left: 114px; top: 802px;
    font-family: "Barlow", sans-serif; font-weight: 400;
    font-size: 28px; letter-spacing: 4px; color: var(--ink-soft);
    white-space: nowrap;
  }
  .capsule-icon { position: absolute; left: 516px; top: 805px; width: 60px; height: 28px; }
</style>
</head>
<body>
  <main class="label">
    <div class="brand">
      <span class="brand-dot"></span>
      <span class="brand-name">NOBLE CALM<sup>®</sup></span>
    </div>

    <svg class="product-art" viewBox="0 0 262 338" role="img" aria-label="Abstract overlapping watercolour shapes in golden yellow and amber, the product's changeable vector art">
      <defs>
        <linearGradient id="art-tone" x1="0" y1="0" x2="1" y2="1">
          <stop offset="0" stop-color="#f4d98a"/>
          <stop offset="0.55" stop-color="#d9913f"/>
          <stop offset="1" stop-color="#e6ba45"/>
        </linearGradient>
      </defs>
      <rect x="0" y="0" width="262" height="338" rx="70" fill="url(#art-tone)" opacity="0.9"/>
    </svg>

    <h1 class="product-name">Magnesium + B6</h1>
    <p class="product-desc">MAGNESIUM WITH GINGER TASTE</p>

    <div class="dosage">
      <span class="count">60</span>
      <span class="unit">capsules</span>
      <span class="divider"></span>
      <span class="intake">Daily intake 1 capsule</span>
    </div>

    <p class="category">DIETARY SUPPLEMENT</p>
    <svg class="capsule-icon" viewBox="0 0 60 28" aria-hidden="true">
      <rect x="2" y="2" width="56" height="24" rx="12" fill="none" stroke="#333" stroke-width="3.5"/>
      <line x1="30" y1="3" x2="30" y2="25" stroke="#333" stroke-width="3.5"/>
    </svg>
  </main>
</body>
</html>
```